Law Firm Website

We are a small California based law firm specializing in business, corporate and litigation matters. We need to have our website redesigned. We are looking for a new and fresh look for our site, keeping in mind that we are a law firm.
What we don't want:
**the traditional "gavel" and "scales of justice" look
**anything too crazy
What we do want:
**sophisticated yet modern and fresh corporate look and feel
**samples of websites we really like:
http://www.tarnwellhope.example
http://www.marrowgate.example/
we also like:
http://www.fenwoodastley.example/
http://www.qz.example/
http://www.brenhollow.example/
http://www.pvdn.example
http://www.nqrlaw.example/
The content will be whatever is currently on our website (www.okabelawgroup.example). We will be selecting the winner based on originality and keeping the above requirements in mind. Please note that the photos that you use will be the ones that we will be using, so choose wisely because the photos will make a difference.
Target Market(s)
Corporate clients
Industry/Entity Type
Law Firm
Look and feel

```html
<!DOCTYPE html>
<html lang="en">
<head>
<meta charset="utf-8">
<title>Okabe Law Group, LLP</title>
<link rel="stylesheet" href="https://fonts.googleapis.com/css2?family=Source+Sans+3:wght@400;600;700&display=swap">
<style>
  :root {
    --ink: #000000;
    --paper: #ffffff;
    --text: #111111;
    --muted: #222222;
    --brand-blue: #2b86d6;
    --hero-grey-light: #eeeff1;
    --hero-grey-dark: #a9abae;
    --dot-grey: #b9b9b9;
    --footer-text: #ffffff;
    --field-hint: #8a8a8a;
  }
  * { box-sizing: border-box; margin: 0; padding: 0; }
  html, body { width: 1200px; height: 1080px; overflow: hidden; }
  body {
    position: relative;
    background: var(--paper);
    color: var(--text);
    font-family: "Source Sans 3", "Myriad Pro", Arial, sans-serif;
  }
  .abs { position: absolute; }

  .top-rule { left: 0; top: 0; width: 1200px; height: 3px; background: var(--ink); }

  .login {
    left: 955px; top: 18px; width: 96px; height: 24px;
    background: var(--ink); color: var(--paper);
    font-size: 15px; line-height: 24px; text-align: center; text-decoration: none;
  }

  .brand-mark { left: 152px; top: 45px; width: 67px; height: 67px; background: var(--brand-blue); }
  .brand-name {
    left: 118px; top: 113px; font-size: 16px; font-weight: 700;
    color: var(--ink); letter-spacing: -0.3px; white-space: nowrap;
  }

  .main-nav { left: 711px; top: 76px; width: 342px; height: 35px; border-bottom: 2px solid var(--ink); }
  .main-nav a {
    position: absolute; top: 10px; font-size: 11.5px; color: var(--ink);
    text-decoration: none; letter-spacing: 0.2px; white-space: nowrap;
  }
  .main-nav a.is-active::before {
    content: ""; position: absolute; left: -1px; top: -10px; width: 37px; height: 2px; background: var(--ink);
  }

  .hero-title { left: 171px; top: 231px; font-size: 30px; font-weight: 400; letter-spacing: 0.2px; color: var(--ink); }
  .hero-copy {
    left: 167px; top: 282px; width: 395px;
    font-size: 19.5px; line-height: 31px; text-align: justify; text-indent: 35px; color: var(--text);
  }
  .read-more {
    left: 398px; top: 422px; width: 169px; height: 55px;
    background: var(--ink); color: var(--paper);
    font-size: 29px; line-height: 55px; text-align: center; text-decoration: none;
  }
  .hero-visual {
    left: 597px; top: 227px; width: 515px; height: 352px;
    background: radial-gradient(ellipse at 55% 40%, var(--hero-grey-light) 0%, #d6d7d9 45%, var(--paper) 80%);
  }
  .slider-dots { left: 581px; top: 556px; display: flex; gap: 12px; }
  .slider-dots span {
    width: 14px; height: 14px; border-radius: 50%;
    background: radial-gradient(circle at 50% 35%, #eaeaea, var(--dot-grey));
  }
  .slider-dots span.is-current { background: radial-gradient(circle at 50% 35%, #777, var(--ink)); }

  .feature { top: 622px; width: 260px; text-align: center; }
  .feature svg { display: block; margin: 0 auto; }
  .feature h2 { margin-top: 12px; font-size: 15px; font-weight: 400; color: var(--ink); }
  .feature p { margin-top: 9px; font-size: 12.5px; line-height: 20.5px; color: var(--muted); }
  .feature--info { left: 122px; }
  .feature--news { left: 473px; }
  .feature--research { left: 816px; }

  .treeline {
    left: 981px; top: 857px; width: 142px; height: 51px;
    background: linear-gradient(to bottom, rgba(0,0,0,0) 0%, rgba(0,0,0,0.55) 40%, var(--ink) 100%);
  }

  .site-footer { left: 0; top: 908px; width: 1200px; height: 172px; background: var(--ink); color: var(--footer-text); }
  .site-footer h3 { position: absolute; top: 38px; font-size: 20px; font-weight: 400; }
  .col-social h3 { left: 99px; }
  .social-links { position: absolute; left: 99px; top: 78px; display: flex; gap: 14px; }
  .social-links span { width: 26px; height: 26px; border-radius: 50%; background: var(--footer-text); }
  .copyright { position: absolute; left: 99px; top: 130px; font-size: 15px; }
  .col-nav h3 { left: 424px; }
  .footer-nav { position: absolute; left: 453px; top: 71px; list-style: none; }
  .footer-nav li { font-size: 16px; line-height: 20.6px; letter-spacing: 0.4px; }
  .footer-nav li::before { content: "// "; }
  .col-news h3 { left: 784px; }
  .newsletter { position: absolute; left: 786px; top: 85px; width: 321px; height: 45px; background: var(--paper); }
  .newsletter .field { position: absolute; left: 10px; top: 13px; font-size: 12.5px; color: var(--field-hint); }
  .newsletter .go { position: absolute; right: 18px; top: 11px; font-size: 16px; color: var(--ink); }
</style>
</head>
<body>
  <div class="abs top-rule"></div>

  <a class="abs login" href="#">LOGIN</a>

  <div class="abs brand-mark"></div>
  <div class="abs brand-name">Okabe Law Group, LLP</div>

  <nav class="abs main-nav">
    <a class="is-active" href="#" style="left:1px">O NAS</a>
    <a href="#" style="left:64px">INDYWIDUALNI</a>
    <a href="#" style="left:175px">KORPORACYJNI</a>
    <a href="#" style="left:288px">KONTAKT</a>
  </nav>

  <h1 class="abs hero-title">FIND LAW ANSWERS</h1>
  <p class="abs hero-copy">Lorem ipsum dolor sit amet, consectetuer adipiscing elit, sed diam nonummy nibh euismod tincidunt ut laoreet dolore magna aliquam erat volutpat.</p>
  <a class="abs read-more" href="#">Read more</a>

  <div class="abs hero-visual" role="img" aria-label="Silver gavel resting on a white surface with a soft shadow"></div>
  <div class="abs slider-dots">
    <span class="is-current"></span><span></span><span></span><span></span>
  </div>

  <section class="abs feature feature--info">
    <svg width="97" height="92" viewBox="0 0 97 92" aria-hidden="true">
      <ellipse cx="48.5" cy="46" rx="48.5" ry="46" fill="#000"/>
      <polygon points="26,36 48.5,22 71,36" fill="#fff"/>
      <rect x="26" y="38" width="45" height="4" fill="#fff"/>
      <rect x="30" y="44" width="6" height="22" fill="#fff"/>
      <rect x="40" y="44" width="6" height="22" fill="#fff"/>
      <rect x="51" y="44" width="6" height="22" fill="#fff"/>
      <rect x="61" y="44" width="6" height="22" fill="#fff"/>
      <rect x="24" y="68" width="49" height="4" fill="#fff"/>
      <rect x="20" y="73" width="57" height="4" fill="#fff"/>
    </svg>
    <h2>INFORMATION</h2>
    <p>Cras justo odio, dapibus ac facilisis<br>in, egestas eget quam. Donec id elit non mi<br>porta gravida.</p>
  </section>

  <section class="abs feature feature--news">
    <svg width="97" height="92" viewBox="0 0 97 92" aria-hidden="true">
      <ellipse cx="48.5" cy="46" rx="48.5" ry="46" fill="#000"/>
      <rect x="47" y="18" width="3" height="52" fill="#fff"/>
      <rect x="25" y="30" width="47" height="2.5" fill="#fff"/>
      <line x1="27" y1="32" x2="20" y2="56" stroke="#fff" stroke-width="1.2"/>
      <line x1="27" y1="32" x2="34" y2="56" stroke="#fff" stroke-width="1.2"/>
      <line x1="70" y1="32" x2="63" y2="56" stroke="#fff" stroke-width="1.2"/>
      <line x1="70" y1="32" x2="77" y2="56" stroke="#fff" stroke-width="1.2"/>
      <path d="M18 56 h18 a9 5 0 0 1 -18 0z" fill="#fff"/>
      <path d="M61 56 h18 a9 5 0 0 1 -18 0z" fill="#fff"/>
      <rect x="37" y="70" width="23" height="4" fill="#fff"/>
    </svg>
    <h2>LATEST NEWS</h2>
    <p>Cras justo odio, dapibus ac facilisis<br>in, egestas eget quam. Donec id elit non mi<br>porta gravida.</p>
  </section>

  <section class="abs feature feature--research">
    <svg width="97" height="92" viewBox="0 0 97 92" aria-hidden="true">
      <ellipse cx="48.5" cy="46" rx="48.5" ry="46" fill="#000"/>
      <rect x="15" y="58" width="40" height="8" fill="#fff"/>
      <rect x="16" y="49" width="38" height="8" fill="#fff"/>
      <rect x="18" y="41" width="34" height="7" fill="#fff"/>
      <rect x="56" y="30" width="8" height="36" fill="#fff"/>
      <rect x="66" y="27" width="9" height="39" fill="#fff"/>
      <rect x="77" y="30" width="7" height="36" fill="#fff"/>
    </svg>
    <h2>RESEARCH</h2>
    <p>Cras justo odio, dapibus ac facilisis<br>in, egestas eget quam. Donec id elit non mi<br>porta gravida.</p>
  </section>

  <div class="abs treeline" role="img" aria-label="Silhouette of a row of pine trees"></div>

  <footer class="abs site-footer">
    <div class="col-social">
      <h3>Social Networks</h3>
      <div class="social-links" aria-label="Social profiles">
        <span></span><span></span><span></span>
      </div>
      <p class="copyright">©2014. All Rights Reserved</p>
    </div>
    <div class="col-nav">
      <h3>Navigation</h3>
      <ul class="footer-nav">
        <li>O nas</li>
        <li>Indywidualni</li>
        <li>Korporacyjni</li>
        <li>Kontakt</li>
      </ul>
    </div>
    <div class="col-news">
      <h3>Newsletter</h3>
      <div class="newsletter">
        <span class="field">Enter your mail</span>
        <span class="go">GO</span>
      </div>
    </div>
  </footer>
</body>
</html>
```